whitening syringe artwork design

3ml syringe with silkscreen printing:
sample:
https://www.quorvashop.example/Velvo-Crane-Whitening-Syringes-Carbamide/dp/Q51842KX93/ref=sr_1_6?crid=7ZP42WQ81LMRT&dchild=1&keywords=whitening+syringes&qid=1698802214&sprefix=whitening+sy%2Caps%2C150&sr=8-6
inside the writing:
"teeth whitening gel " change to "Orvanne WHITENING GEL"
"Advanced formula" change to our logo and "Not all gels are created equal. "

additional requirements:
Inches: 2.01" wide x 1.34" around

CM: 5.1cm wide x 3.4cm around

See attached template: Generic_Syringe Labels 3ml_Silkscreen.pdf

- Leave the volume gage where it is, so it prints correctly on the syringe

- Feel free to change the color and font style

- An "identifying marker" is required: Teeth Whitening Syringe or Teeth Whitening Gel (for example)

- Replace "Teeth Whitening Gel - Advanced Formula" with your text and logo - it is there as a placeholder

-We require PDF files created to print ready specifications. Color images should be down-sampled to 300DPI

-Please provide us your Tintora color references for the color used in your artwork

https://www.tintora.example/color-finder#/pick?tintoraBook=tintoraSolidCoatedV3M2

-Please ensure that all fonts are embedded in the PDF document or make sure you convert fonts to outlines to prevent any issues with fonts (AI-Type-Create Outlines)

We will need your print ready artwork in a high resolution PDF file

teeth whitening ecommerce

• follow the guide document, and add text I want, color code from Tintora is provided

```html
<!DOCTYPE html>
<html lang="en">
<head>
<meta charset="utf-8">
<title>Whitening Syringe Silkscreen Labels</title>
<link rel="stylesheet" href="https://fonts.googleapis.com/css2?family=Yellowtail&family=Montserrat:wght@600&family=Barlow+Condensed:wght@500;700&display=swap">
<style>
  :root {
    --paper: #ffffff;
    --navy: #28235f;
    --blue: #1e72b9;
    --ink: #1f3f8c;
    --white: #ffffff;
    --rim-dark: #4a4a4a;
    --rim-light: #f2f2f2;
  }
  html, body {
    margin: 0;
    padding: 0;
    width: 1200px;
    height: 718px;
    overflow: hidden;
    background: var(--paper);
  }
  .artboard { display: block; width: 1200px; height: 718px; }
  .brand-name {
    font-family: "Montserrat", sans-serif;
    font-weight: 600;
    font-size: 14px;
    letter-spacing: 3px;
    fill: var(--white);
  }
  .product-title {
    font-family: "Yellowtail", "Brush Script MT", cursive;
    fill: var(--white);
  }
  .gauge-tick { stroke: var(--ink); stroke-width: 3; }
  .gauge-label {
    font-family: "Barlow Condensed", sans-serif;
    font-weight: 700;
    font-size: 24px;
    fill: var(--ink);
  }
  .gauge-label.small { font-size: 22px; }
  .gauge-unit {
    font-family: "Barlow Condensed", sans-serif;
    font-weight: 500;
    font-size: 22px;
    fill: var(--ink);
  }
</style>
</head>
<body>
<svg class="artboard" viewBox="0 0 1200 718" xmlns="http://www.w3.org/2000/svg">
  <defs>
    <linearGradient id="label-fill" x1="0" y1="0" x2="1" y2="0">
      <stop offset="0" stop-color="var(--navy)"/>
      <stop offset="1" stop-color="var(--blue)"/>
    </linearGradient>
    <linearGradient id="label-rim" x1="0" y1="0" x2="0" y2="1">
      <stop offset="0" stop-color="var(--rim-dark)"/>
      <stop offset="0.3" stop-color="var(--rim-light)"/>
      <stop offset="0.7" stop-color="var(--rim-light)"/>
      <stop offset="1" stop-color="var(--rim-dark)"/>
    </linearGradient>
  </defs>

  <g class="pen-label">
    <ellipse cx="307" cy="245" rx="220" ry="67" fill="url(#label-fill)" stroke="url(#label-rim)" stroke-width="4"/>
    <text class="brand-name" x="307" y="202" text-anchor="middle">TOVARA</text>
    <text class="product-title" x="307" y="262" text-anchor="middle" font-size="44" textLength="356" lengthAdjust="spacingAndGlyphs">Mirelle Whitening Pen</text>
  </g>

  <g class="pen-label">
    <ellipse cx="299" cy="475" rx="220" ry="67" fill="url(#label-fill)" stroke="url(#label-rim)" stroke-width="4"/>
    <text class="brand-name" x="299" y="432" text-anchor="middle">TOVARA</text>
    <text class="product-title" x="299" y="492" text-anchor="middle" font-size="44" textLength="356" lengthAdjust="spacingAndGlyphs">Mirelle Whitening Pen</text>
  </g>

  <g class="gel-label">
    <ellipse cx="885" cy="300" rx="207" ry="63" fill="url(#label-fill)" stroke="url(#label-rim)" stroke-width="4"/>
    <text class="brand-name" x="885" y="260" text-anchor="middle">TOVARA</text>
    <text class="product-title" x="885" y="318" text-anchor="middle" font-size="44" textLength="330" lengthAdjust="spacingAndGlyphs">Teeth Whitening Gel</text>
  </g>

  <g class="volume-gauge">
    <line class="gauge-tick" x1="658" y1="424" x2="658" y2="487"/>
    <line class="gauge-tick" x1="727" y1="449" x2="727" y2="487"/>
    <line class="gauge-tick" x1="796" y1="424" x2="796" y2="487"/>
    <line class="gauge-tick" x1="876" y1="449" x2="876" y2="487"/>
    <line class="gauge-tick" x1="955" y1="424" x2="955" y2="487"/>
    <line class="gauge-tick" x1="1024" y1="449" x2="1024" y2="487"/>
    <line class="gauge-tick" x1="1093" y1="424" x2="1093" y2="487"/>

    <text class="gauge-label small" transform="translate(736 428) rotate(-90)">½</text>
    <text class="gauge-label" transform="translate(805 418) rotate(-90)">1</text>
    <text class="gauge-label small" transform="translate(885 440) rotate(-90)">1½</text>
    <text class="gauge-label" transform="translate(964 418) rotate(-90)">2</text>
    <text class="gauge-label small" transform="translate(1033 442) rotate(-90)">2½</text>
    <text class="gauge-label" transform="translate(1102 418) rotate(-90)">3</text>
    <text class="gauge-unit" transform="translate(1115 482) rotate(-90)">ml/cc</text>
  </g>
</svg>
</body>
</html>
```